QRV Advisors needs a web site

We need a web site for www.qrvadvisors-example.com. QRV is a mergers and acquisition consulting company that focuses our buyer and seller services on logistics companies. We help put companies together, and help with legal and financial due diligence. We want the web site to express our service and show the logistics components. We want personalized images versus pictures of trucks and airplanes.

Our new logo uses Burgandy and grey colors. Image attached. We are not in to bold, big letters...classy, artistic, low key preferred. Confidentiality, experience, professional are what we want to express on the site.

All we expect for the first part of this project is a home page, and one subpage.  We are budgeting other funds for the technical aspects of the web site

Reason: All that I'm seeing so far is trucks, forklifts and planes. We are a legal mergers and acquisitions firm that focus on logistics. I like some of the images to say logistics, but really want it say legal, financial, and putting companies together. Will pay extra for the sub page if someone can impress us with a home page.

Reason: Swamped with another project at the moment...will work on this over the weekend and provide designer feedback and select final design by Tuesday

```html
<!DOCTYPE html>
<html lang="en">
<head>
<meta charset="utf-8">
<title>QRV Advisors – Home</title>
<link rel="stylesheet" href="https://fonts.googleapis.com/css2?family=Open+Sans:wght@400;600&family=Roboto:wght@400;500;700&display=swap">
<style>
:root{
  --burgundy:#a30034;
  --burgundy-dark:#8e002c;
  --charcoal:#3b3b3b;
  --slate:#5a5a5a;
  --text:#3d3d3d;
  --muted:#777;
  --line:#c9c9c9;
  --header-bg:#efefef;
  --white:#fff;
}
*{box-sizing:border-box;margin:0;padding:0}
html,body{width:1004px;height:1200px;overflow:hidden;background:var(--white)}
body{position:relative;font-family:"Open Sans",Arial,sans-serif;color:var(--text);font-size:11px}
.abs{position:absolute}

/* header */
.top-strip{left:0;top:0;width:1004px;height:6px;background:var(--slate)}
.site-header{left:0;top:6px;width:1004px;height:116px;background:linear-gradient(90deg,#e9e9e9,#f4f4f4 40%,#ececec)}
.brand{left:117px;top:38px;display:flex;align-items:center;gap:10px}
.brand-mark{width:14px;height:14px;background:var(--burgundy)}
.brand-name{font-family:"Roboto",sans-serif;font-weight:500;font-size:40px;letter-spacing:6px;color:var(--slate);line-height:1}
.brand-tag{left:262px;top:41px;font-family:"Roboto",sans-serif;font-weight:500;font-size:14px;line-height:14px;color:var(--slate);letter-spacing:1px;border-left:2px solid var(--slate);padding-left:10px}
.call{left:744px;top:20px;display:flex;gap:6px;align-items:center}
.call-label{font-size:11px;color:#333;line-height:13px}
.call-number{font-family:"Roboto",sans-serif;font-weight:700;font-size:18px;color:var(--burgundy);line-height:20px}
.main-nav{left:447px;top:75px;display:flex;gap:16px}
.main-nav a{font-size:11.5px;color:#666;text-decoration:none;padding:5px 2px 6px;border-top:1px solid var(--line);border-bottom:1px solid var(--line)}
.main-nav a.current{color:var(--burgundy);font-weight:600;position:relative}
.main-nav a.current::before{content:"";position:absolute;left:50%;top:-1px;margin-left:-4px;border:4px solid transparent;border-top-color:var(--slate)}

/* hero */
.hero{left:0;top:125px;width:1004px;height:371px;background:linear-gradient(180deg,#dfe3e6 0%,#b9bec2 45%,#6d7073 100%)}
.hero-arrow{width:30px;height:30px;border-radius:50%;background:rgba(30,30,30,.85);display:flex;align-items:center;justify-content:center}
.hero-caption{left:572px;top:378px;width:432px;height:118px;background:rgba(70,70,70,.75);padding:8px 0 0 8px}
.hero-caption h1{font-family:"Roboto",sans-serif;font-weight:700;font-size:23px;line-height:29px;color:var(--white);letter-spacing:.5px}

/* services */
.services{left:0;top:496px;width:1004px;height:226px;background:linear-gradient(180deg,#4a4a4a,#2f2f2f)}
.service{width:160px;text-align:center;top:25px}
.service-icon{width:118px;height:118px;border-radius:50%;background:var(--burgundy);margin:0 auto;display:flex;align-items:center;justify-content:center}
.service h3{font-family:"Roboto",sans-serif;font-weight:500;font-size:14.5px;color:var(--white);margin-top:12px}
.service p{font-size:10px;line-height:15px;color:#e6e6e6;margin-top:5px}
.band-arrow{top:68px}

/* content columns */
.col-title{font-family:"Roboto",sans-serif;font-weight:700;font-size:16.5px;color:var(--slate);top:748px;width:236px;padding-bottom:6px;border-bottom:1px dashed #aaa}
.col-title span{color:var(--burgundy)}
.about-photo{left:118px;top:785px;width:235px;height:101px;border:4px solid var(--burgundy);background:linear-gradient(90deg,#c9c3bd,#e8e4df 50%,#8f8a86)}
.about-text{left:119px;top:898px;width:236px;font-size:10px;line-height:15.5px;color:#333;text-align:justify}
.read-more{font-family:"Roboto",sans-serif;font-weight:700;font-size:10px;color:var(--burgundy);text-decoration:none}
.news-item{left:386px;width:234px;border-bottom:1px dotted #ddd;padding-bottom:6px}
.news-meta{font-size:10px;color:var(--burgundy)}
.news-item p{font-size:10px;line-height:16px;letter-spacing:.6px;color:#333}
.news-item .read-more{display:block;text-align:right;margin-top:3px}
.field-label{left:654px;font-size:11px;color:#444}
.field{left:710px;width:176px;height:18px;border:1px solid #bbb;background:var(--white)}
.submit{left:710px;top:972px;width:87px;height:21px;background:var(--burgundy);color:var(--white);font-family:"Roboto",sans-serif;font-weight:700;font-size:13px;border:0;letter-spacing:.5px}

/* footer */
.site-footer{left:0;top:1032px;width:1004px;height:168px;background:var(--burgundy);border-top:4px solid #6a6a6a}
.foot-title{font-family:"Roboto",sans-serif;font-weight:500;font-size:12.5px;color:var(--white);top:1050px;padding-bottom:5px;border-bottom:1px dotted rgba(255,255,255,.7)}
.foot-links{left:118px;top:1077px;list-style:none}
.foot-links li{font-size:10px;color:var(--white);line-height:18.4px}
.foot-links li::before{content:"›";margin-right:7px}
.foot-divider{top:1052px;width:1px;height:128px;background:rgba(255,255,255,.3)}
.foot-contact{left:272px;display:flex;gap:12px;font-size:10px;color:var(--white);line-height:14px}
.newsletter-copy{left:514px;top:1078px;width:180px;font-size:10px;line-height:15px;color:var(--white)}
.email-input{left:512px;top:1114px;width:169px;height:19px;background:var(--white);border-radius:3px;font-size:9.5px;color:#888;padding:3px 0 0 25px}
.subscribe{left:513px;top:1145px;width:67px;height:19px;background:#4d4d4d;color:var(--white);font-family:"Roboto",sans-serif;font-weight:700;font-size:11px;text-align:center;line-height:19px;border-radius:2px}
.foot-brand{left:712px;top:1046px;font-family:"Roboto",sans-serif;font-weight:500;font-size:52px;letter-spacing:10px;color:#7a7a7a;line-height:1}
.social{top:1120px;width:21px;height:21px;border-radius:3px;background:#3b6fc0}
.copyright{left:710px;top:1154px;width:186px;text-align:center;font-size:10px;line-height:15px;color:var(--white)}
</style>
</head>
<body>

<div class="abs top-strip"></div>
<header class="abs site-header"></header>
<div class="abs brand"><span class="brand-mark"></span><span class="brand-name">QRV</span></div>
<div class="abs brand-tag">QUAY RIDGE<br>VENTURES</div>
<div class="abs call">
  <svg width="26" height="26" viewBox="0 0 26 26"><circle cx="13" cy="13" r="11.5" fill="none" stroke="#a30034" stroke-width="1.5"/><path d="M10 7c-2 1-2 4 0 8s5 6 7 5l1-2-3-2-1 1c-1 0-3-3-3-4l1-1-1-3z" fill="#a30034"/></svg>
  <div><div class="call-label">Call Us Today</div><div class="call-number">555 014 2368</div></div>
</div>
<nav class="abs main-nav">
  <a class="current">Home</a><a>About Us</a><a>Consulting Services</a><a>News &amp; Events</a><a>FAQ's</a><a>Contact Us</a>
</nav>

<section class="abs hero" role="img" aria-label="Photo of a consultant presenting to a business team in a bright boardroom"></section>
<div class="abs hero-arrow" style="left:123px;top:284px"><svg width="10" height="12"><path d="M7 1L2 6l5 5" fill="none" stroke="#fff" stroke-width="1.5"/></svg></div>
<div class="abs hero-arrow" style="left:851px;top:284px"><svg width="10" height="12"><path d="M3 1l5 5-5 5" fill="none" stroke="#fff" stroke-width="1.5"/></svg></div>
<div class="abs hero-caption"><h1>We Are Mergers &amp;<br>Acquisition&nbsp; Technology<br>Consulting Company.</h1></div>

<section class="abs services">
  <svg class="abs band-arrow" style="left:94px" width="14" height="26"><path d="M12 1L2 13l10 12" fill="none" stroke="#999" stroke-width="2"/></svg>
  <svg class="abs band-arrow" style="left:890px" width="14" height="26"><path d="M2 1l10 12L2 25" fill="none" stroke="#999" stroke-width="2"/></svg>

  <div class="abs service" style="left:134px">
    <div class="service-icon"><svg width="64" height="64" viewBox="0 0 64 64" fill="#fff"><rect x="6" y="34" width="4" height="22"/><rect x="13" y="28" width="4" height="28"/><rect x="20" y="36" width="4" height="20"/><rect x="27" y="30" width="4" height="26"/><rect x="34" y="40" width="4" height="16"/><rect x="4" y="56" width="38" height="2"/><circle cx="34" cy="18" r="11" fill="none" stroke="#fff" stroke-width="4"/><path d="M41 26l14 14-3 3-14-14z"/></svg></div>
    <h3>Business Analysis</h3><p>Lorem ipsum dolor sit ameteuis<br>tincidunt ut laoreet amte</p>
  </div>
  <div class="abs service" style="left:326px">
    <div class="service-icon"><svg width="72" height="50" viewBox="0 0 72 50" fill="#fff"><circle cx="14" cy="12" r="7"/><circle cx="58" cy="12" r="7"/><circle cx="36" cy="9" r="8"/><path d="M2 44c0-14 4-20 12-20s12 6 12 20z"/><path d="M46 44c0-14 4-20 12-20s12 6 12 20z"/><path d="M22 46c0-17 5-24 14-24s14 7 14 24z"/></svg></div>
    <h3>Business Intelligence</h3><p>Lorem ipsum dolor sit ameteuis<br>tincidunt ut laoreet amte</p>
  </div>
  <div class="abs service" style="left:518px">
    <div class="service-icon"><svg width="50" height="76" viewBox="0 0 50 76" fill="#fff"><path d="M25 2L8 34h11v8C19 55 10 64 4 74h13c4-7 8-13 8-20 0 7 4 13 8 20h13c-6-10-15-19-15-32v-8h11z"/></svg></div>
    <h3>Mergers</h3><p>Lorem ipsum dolor sit ameteuis<br>tincidunt ut laoreet amte</p>
  </div>
  <div class="abs service" style="left:710px">
    <div class="service-icon"><svg width="72" height="58" viewBox="0 0 72 58" fill="#fff"><path d="M44 2l26 20-26 20V32H30V12h14z"/><path d="M28 16L2 36l26 20V46h14V26H28z"/></svg></div>
    <h3>Acquisition</h3><p>Lorem ipsum dolor sit ameteuis<br>tincidunt ut laoreet amte</p>
  </div>
</section>

<h2 class="abs col-title" style="left:119px"><span>ABOUT</span> COMPANY</h2>
<div class="abs about-photo" role="img" aria-label="Group photo of the advisory team in business attire"></div>
<p class="abs about-text">QRV assists business owners within the logistics industry to implement growth and exit strategies. We offer business planning and merger and acquisition(M&amp;A) advisory services. QRV services are offered by industry executives with extensive M&amp;A experience..</p>
<a class="abs read-more" style="left:294px;top:984px">Read More »</a>

<h2 class="abs col-title" style="left:387px"><span>NEWS &amp;</span> EVENTS</h2>
<article class="abs news-item" style="top:783px"><div class="news-meta">8-10-2014 | By Admin</div><p>Lorem ipsum dolor sit amet, consectetuer adipiscing elit, sed diam...</p><a class="read-more">Read More »</a></article>
<article class="abs news-item" style="top:859px"><div class="news-meta">8-10-2014 | By Admin</div><p>Lorem ipsum dolor sit amet, consectetuer adipiscing elit, sed diam...</p><a class="read-more">Read More »</a></article>
<article class="abs news-item" style="top:938px;border-bottom:0"><div class="news-meta">8-10-2014 | By Admin</div><p>Lorem ipsum dolor sit amet, consectetuer adipiscing elit, sed diam...</p><a class="read-more">Read More »</a></article>

<h2 class="abs col-title" style="left:652px"><span>CONTACT</span> US</h2>
<label class="abs field-label" style="top:787px">Name</label><div class="abs field" style="top:785px"></div>
<label class="abs field-label" style="top:822px">Phone</label><div class="abs field" style="top:820px"></div>
<label class="abs field-label" style="top:857px">Email</label><div class="abs field" style="top:855px"></div>
<label class="abs field-label" style="top:892px">Message</label><div class="abs field" style="top:890px;height:58px"></div>
<button class="abs submit">SUBMIT</button>

<footer class="abs site-footer"></footer>
<h3 class="abs foot-title" style="left:118px;width:111px">QUICK LINKS</h3>
<ul class="abs foot-links"><li>Home</li><li>About Us</li><li>Consulting Services</li><li>News &amp; Events</li><li>FAQ's</li><li>Contact Us</li></ul>
<div class="abs foot-divider" style="left:245px"></div>
<h3 class="abs foot-title" style="left:272px;width:190px">CONTACT US</h3>
<div class="abs foot-contact" style="top:1078px"><svg width="14" height="18" viewBox="0 0 14 18"><path d="M7 1a5.5 5.5 0 0 0-5.5 5.5C1.5 11 7 17 7 17s5.5-6 5.5-10.5A5.5 5.5 0 0 0 7 1zm0 8a2.3 2.3 0 1 1 0-4.6A2.3 2.3 0 0 1 7 9z" fill="#fff"/></svg><span>Lorem ipsum dolor sit ameteuismo<br>tincidunt ut laoreet dolore my amte,</span></div>
<div class="abs foot-contact" style="top:1119px"><svg width="14" height="14" viewBox="0 0 14 14"><path d="M3 1C1 2 1 5 3 8s5 5 7 5l2-2-3-2-1 1C7 10 4 7 4 6l1-1-2-4z" fill="#fff"/></svg><span>555-014-2368</span></div>
<div class="abs foot-contact" style="top:1148px"><svg width="14" height="12" viewBox="0 0 14 12"><rect x=".5" y="1.5" width="13" height="9" fill="#fff"/><path d="M.5 1.5L7 7l6.5-5.5" fill="none" stroke="#a30034"/></svg><span>info@quayridgeventures-example.com</span></div>
<div class="abs foot-divider" style="left:489px"></div>
<h3 class="abs foot-title" style="left:514px;width:178px">NEWSLETTER</h3>
<p class="abs newsletter-copy">Subscribe to our newsletter to receive our special offers , discounts &amp; more.</p>
<div class="abs email-input">your e-mail address</div>
<div class="abs subscribe">Subscribe</div>
<div class="abs foot-brand">QRV</div>
<span class="abs social" style="left:766px"></span>
<span class="abs social" style="left:795px;background:#4aa8e0"></span>
<span class="abs social" style="left:824px;background:#2b7bb9"></span>
<p class="abs copyright">© 2014 Quayridgeventures-example.com.<br>All Rights Reserved</p>

</body>
</html>
```